Website Home Page Main Banner Design (wholesale)

1170 x 547 PNG web banner design

Varnel Global Corporation is a full-service importer based out of New York City, New York. For over 50 years, we have offered our customers fashionable, quality products at competitive prices. The company has a full in-house development and design staff, with a 100,000 sq. foot warehouse in Perth Amboy, New Jersey. Our talented design team, with extensive overseas sourcing experience, is always on the search for innovative ideas and hot new products.

Varnel currently consists of the following divisions– Toddler Novelty Company (TNC), Hair Accessories, Jewelry (Gleamor), General Merchandise (Brandolux), Beauty Implements, Socks & Hosiery and Electronics.

Website- https://varnel.quorblend.example/index.php/

Target Market(s)

Retailers

Industry/Entity Type

Wholesale

Number of Pages Required

1 page

Font styles to use
Serif

Colors

Designer to choose colors to be used in the design.

Requirements
Must have
• Company Name- Varnel Global Corp
Nice to have
• Some of the products featured on the site
Should not have
• Nothing

```html
<!DOCTYPE html>
<html lang="en">
<head>
<meta charset="utf-8">
<title>Varnel Global Corp – Home Banner</title>
<link href="https://fonts.googleapis.com/css2?family=Open+Sans:wght@300;400;600&family=Dancing+Script:wght@700&display=swap" rel="stylesheet">
<style>
  :root {
    --paper-light: #f7f7f7;
    --paper-mid: #ececec;
    --brand-violet: #8c84d2;
    --ink-dark: #1e1e1e;
    --ink-grey: #5a5a5a;
    --accent-magenta: #cf1a84;
    --rule-grey: #bdbdbd;
  }
  * { margin: 0; padding: 0; box-sizing: border-box; }
  html, body { width: 1200px; height: 561px; overflow: hidden; }
  body { font-family: "Open Sans", Arial, sans-serif; }

  .banner { position: relative; width: 1200px; height: 561px; overflow: hidden; }

  .paper-texture {
    position: absolute; inset: 0;
    background: radial-gradient(ellipse at 50% 45%, var(--paper-light) 0%, var(--paper-mid) 100%);
  }

  .brand {
    position: absolute; top: 68px; left: 0; width: 100%;
    text-align: center;
    font-size: 50px; font-weight: 600; line-height: 1;
    color: var(--brand-violet);
    letter-spacing: 1px;
  }

  .founded {
    position: absolute; top: 177px; left: 0; width: 100%;
    text-align: center; font-size: 15px; color: var(--ink-dark);
  }

  .tagline {
    position: absolute; top: 232px; left: 500px; width: 200px;
    text-align: center; color: var(--ink-dark);
  }
  .tagline .ruled {
    display: flex; align-items: center; justify-content: space-between;
    font-size: 16px; line-height: 22px;
  }
  .tagline .ruled::before,
  .tagline .ruled::after {
    content: ""; width: 66px; height: 1px; background: var(--ink-dark);
  }
  .tagline .one-stop {
    font-size: 24px; font-weight: 300; color: var(--ink-grey);
    line-height: 30px; letter-spacing: -0.3px;
  }
  .tagline .for-retailers {
    font-family: "Dancing Script", "Brush Script MT", cursive;
    font-size: 42px; font-weight: 700; color: var(--accent-magenta);
    line-height: 40px; margin-top: -2px;
  }
  .tagline .fashion {
    font-size: 30px; font-weight: 400; line-height: 36px; letter-spacing: -0.5px;
  }
  .tagline .industry {
    font-size: 18px; font-weight: 400; color: var(--ink-grey);
    line-height: 22px; letter-spacing: -0.2px;
  }

  .categories {
    position: absolute; top: 464px; left: 60px; width: 1080px; height: 34px;
    display: flex; align-items: center; justify-content: center;
    list-style: none;
    border-top: 1px solid var(--rule-grey);
    border-bottom: 1px solid var(--rule-grey);
    font-size: 17px; color: var(--accent-magenta); letter-spacing: -0.2px;
  }
  .categories li + li::before {
    content: "|"; margin: 0 18px;
  }
</style>
</head>
<body>
  <main class="banner">
    <div class="paper-texture" role="img" aria-label="Soft white crumpled paper texture background"></div>

    <div class="brand">Varnel</div>
    <p class="founded">FOUNDED IN 1961</p>

    <div class="tagline">
      <div class="ruled">THE</div>
      <div class="one-stop">ONE-STOP-SHOP</div>
      <div class="for-retailers">for Retailers</div>
      <div class="ruled">IN</div>
      <div class="fashion">THE FASHION</div>
      <div class="industry">ACCESSORY INDUSTRY</div>
    </div>

    <ul class="categories">
      <li>INFANT SPECIALTY</li>
      <li>HAIR ACCESSORIES</li>
      <li>JEWELRY</li>
      <li>SOCKS</li>
      <li>HBA</li>
      <li>GENERAL MERCHANDISE</li>
    </ul>
  </main>
</body>
</html>
```